New letter head for Air Conditioning business

We need a new professional letter head design to suit our new re-branded air conditioning business. Our new logo is attached

```html
<!DOCTYPE html>
<html lang="en">
<head>
<meta charset="utf-8">
<title>Norvale Air Conditioning &amp; Refrigeration – Letterhead</title>
<link href="https://fonts.googleapis.com/css2?family=Questrial&family=Montserrat:wght@600&display=swap" rel="stylesheet">
<style>
  :root {
    --paper: #f4f4f4;
    --ink: #2b2b2b;
    --charcoal: #333336;
    --green: #4caf6e;
    --red: #e0584e;
    --rule: #555555;
  }
  * { box-sizing: border-box; margin: 0; padding: 0; }
  html, body { width: 971px; height: 1200px; overflow: hidden; }
  body {
    background: var(--paper);
    font-family: "Questrial", "Century Gothic", sans-serif;
    color: var(--ink);
  }
  .letterhead { position: relative; width: 971px; height: 1200px; }

  .brand {
    position: absolute; top: 62px; left: 0; width: 100%;
    display: flex; justify-content: center; align-items: center; gap: 18px;
  }
  .brand-mark { width: 46px; height: 46px; background: var(--green); }
  .brand-text { display: flex; flex-direction: column; }
  .brand-name {
    font-size: 50px; letter-spacing: 6px; color: var(--charcoal); line-height: 1;
  }
  .brand-tagline {
    margin-top: 6px; font-family: "Montserrat", sans-serif; font-weight: 600;
    font-size: 11.5px; letter-spacing: 2.2px; color: var(--green);
  }

  .recipient {
    position: absolute; top: 284px; left: 53px;
    font-size: 16px; line-height: 24.5px;
  }
  .body-copy {
    position: absolute; top: 398px; left: 53px; width: 865px;
    font-size: 16px; line-height: 24.5px; text-align: justify;
  }
  .body-copy p { margin-bottom: 27px; }
  .body-copy p.tight { margin-bottom: 18px; }
  .closing { font-size: 16px; }
  .signature {
    margin-top: 18px; width: 170px; height: 58px;
    background: linear-gradient(90deg, #dcdcdc, #ececec);
  }

  .footer-rule {
    position: absolute; top: 1078px; left: 53px; width: 865px;
    border-top: 1.5px solid var(--rule);
  }
  .contacts {
    position: absolute; top: 1108px; left: 53px; width: 865px;
    display: flex; justify-content: space-between; font-size: 18px; line-height: 27px;
  }
  .contact-group { display: flex; flex-direction: column; }
  .contact-group.divided { border-left: 2px solid var(--green); padding-left: 20px; }
  .contact-item { display: flex; align-items: center; gap: 10px; }
  .contact-item svg { width: 14px; height: 14px; flex: none; }

  .base-band { position: absolute; left: 0; bottom: 0; width: 971px; height: 14px; }
</style>
</head>
<body>
<main class="letterhead">
  <header class="brand">
    <div class="brand-mark"></div>
    <div class="brand-text">
      <span class="brand-name">NORVALE</span>
      <span class="brand-tagline">AIR CONDITIONING &amp; REFRIGERATION</span>
    </div>
  </header>

  <address class="recipient" style="font-style:normal">
    Mr/s<br>First Name and Last Name<br>Company Name<br>Address
  </address>

  <section class="body-copy">
    <p>Lorem Ipsum is simply dummy text of the printing and typesetting industry. Lorem Ipsum has been the industry's standard dummy text ever since the 1500s, when an unknown printer took a galley of type and scrambled it to make a type specimen book. It has survived not only five centuries, but also the leap into electronic typesetting, remaining essentially unchanged. It was popularised in the 1960s with the release of Letraset sheets containing Lorem Ipsum passages.</p>
    <p class="tight">he standard chunk of Lorem Ipsum used since the 1500s is reproduced below for those interested. Sections 1.10.32 and 1.10.33 from "de Finibus Bonorum et Malorum" by Cicero are also reproduced in their exact original form, accompanied by English versions from the 1914 translation by H. Rackham. Lorem ipsum dolor sit amet, consectetur adipiscing elit, sed do eiusmod tempor incididunt ut labore et dolore magna aliqua.</p>
    <p class="tight">It is a long established fact that a reader will be distracted by the readable content of a page when looking at its layout. The point of using Lorem Ipsum is that it has a more-or-less normal distribution of letters, as opposed to using 'Content here, content here', making it look like readable English. Many desktop publishing packages and web page editors now .</p>
    <div class="closing">Your Sincerely,</div>
    <div class="signature" role="img" aria-label="Handwritten signature"></div>
  </section>

  <div class="footer-rule"></div>

  <footer class="contacts">
    <div class="contact-group">
      <span class="contact-item">
        <svg viewBox="0 0 16 16"><path fill="#e0584e" d="M3 1l3 3-1.5 2a9 9 0 0 0 5.5 5.5L12 10l3 3-2 2C7 15 1 9 1 3z"/></svg>
        760-555-0148
      </span>
      <span class="contact-item">
        <svg viewBox="0 0 16 16"><rect x="1" y="3" width="14" height="10" fill="#e0584e"/><path d="M1 3l7 6 7-6" stroke="#f4f4f4" stroke-width="1.5" fill="none"/></svg>
        info@norvaleair.com
      </span>
    </div>
    <div class="contact-group divided">
      <span class="contact-item">
        <svg viewBox="0 0 16 16"><rect x="4" y="1" width="8" height="4" fill="#e0584e"/><rect x="1" y="6" width="14" height="6" rx="1" fill="#e0584e"/><rect x="4" y="10" width="8" height="5" fill="#e0584e" stroke="#f4f4f4"/></svg>
        760-555-0172
      </span>
      <span class="contact-item">
        <svg viewBox="0 0 16 16"><circle cx="8" cy="8" r="7" fill="#e0584e"/><path d="M1 8h14M8 1c-3 4-3 10 0 14M8 1c3 4 3 10 0 14" stroke="#f4f4f4" fill="none"/></svg>
        www.norvaleair.com
      </span>
    </div>
    <div class="contact-group divided">
      <span>4820 Cedar Ridge Road, Suite 210</span>
      <span>Fallbrook, CA 92099</span>
    </div>
  </footer>

  <svg class="base-band" viewBox="0 0 971 14" preserveAspectRatio="none">
    <polygon points="0,0 480,0 466,14 0,14" fill="#4caf6e"/>
    <polygon points="488,0 971,0 971,14 474,14" fill="#e0584e"/>
  </svg>
</main>
</body>
</html>
```